Luxury Business Card Design for High-End Window Treatments

Gilded Slatworks
Custom Plantation Shutters & Architectural Shading Systems

⸻

BACK

Daniel Trevick
Owner

Custom Interior & Exterior Window Treatments

919-555-0148
gildedslatworks.com

I have included a picture that I’m hoping we can use on the back, but I’m also wondering if you can get rid of the ladder? Should we get rid of shutters , shades and blinds underneath Gilded Slatworks?

Target Market(s)

High-end residential homeowners, custom home builders, architects, interior designers, and luxury renovation clients seeking premium plantation shutters and motorized architectural shading systems.

Industry/Entity Type

Custom Window treatments

Contact Information for Business Card

Front Gilded Slatworks Custom Plantation Shutters Motorized Architectural Shading Systems BACK Daniel Trevick Owner 919-555-0148 GildedSlatworks.com Custom Interior & Exterior Window Treatments By Appointment

Requirements
Nice to have
• Not 100% sure on nice to halves or the color but you can definitely check out my website to get a better understanding of what I’m trying to do

```html
<!DOCTYPE html>
<html lang="en">
<head>
<meta charset="utf-8">
<title>Gilded Slatworks – Business Card</title>
<link rel="stylesheet" href="https://fonts.googleapis.com/css2?family=Libre+Baskerville:wght@400;700&family=Montserrat:wght@400;500&display=swap">
<style>
  :root {
    --backdrop: #2b2b2d;
    --card-gold: #a8955f;
    --card-black: #060606;
    --ivory: #f1ece0;
    --gold-bright: #f0cd5a;
    --gold-text: #c9a94a;
    --white: #ffffff;
  }
  * { box-sizing: border-box; margin: 0; padding: 0; }
  html, body {
    width: 1200px; height: 875px; overflow: hidden;
    background: var(--backdrop);
  }
  .canvas { position: relative; width: 1200px; height: 875px; }

  .card {
    position: absolute;
    width: 560px; height: 320px;
    border-radius: 18px;
    box-shadow: 0 18px 40px rgba(0,0,0,.45);
  }
  .card--front { left: 40px; top: 110px; background: var(--card-gold); }
  .card--back  { left: 600px; top: 445px; background: var(--card-black); }

  .brand-name {
    font-family: "Libre Baskerville", serif;
    font-weight: 400;
    line-height: 1.05;
  }
  .tagline {
    font-family: "Libre Baskerville", serif;
    font-weight: 700;
    display: flex;
  }

  .card--front .brand {
    position: absolute; left: 0; right: 0; top: 92px; text-align: center;
  }
  .card--front .brand-name { color: var(--ivory); font-size: 50px; }
  .card--front .tagline {
    color: var(--gold-bright); font-size: 22px; gap: 26px;
    justify-content: center; margin-top: 18px;
  }

  .card--back .brand {
    position: absolute; left: 36px; top: 110px; width: 250px; text-align: center;
  }
  .card--back .brand-name { color: var(--gold-text); font-size: 34px; }
  .card--back .tagline {
    color: var(--gold-text); font-size: 14px; gap: 14px;
    justify-content: center; margin-top: 12px;
  }

  .divider {
    position: absolute; left: 300px; top: 56px;
    width: 2px; height: 208px; background: var(--white);
  }

  .contact {
    position: absolute; left: 324px; top: 60px; width: 220px;
    font-family: "Montserrat", sans-serif; color: var(--white);
  }
  .contact-name {
    font-family: "Libre Baskerville", serif; font-weight: 700;
    color: var(--gold-text); font-size: 21px; margin-bottom: 4px;
  }
  .contact-role { font-size: 13px; margin-bottom: 6px; }
  .contact-service { font-size: 13px; line-height: 1.3; margin-bottom: 14px; }
  .contact-line {
    display: flex; align-items: center; gap: 8px;
    font-size: 13px; margin-bottom: 8px;
  }
  .contact-line svg { width: 13px; height: 13px; flex: none; }
  .contact-note { color: var(--gold-text); font-size: 13px; margin-top: 6px; }
</style>
</head>
<body>
<main class="canvas">

  <section class="card card--front" aria-label="Card front">
    <div class="brand">
      <p class="brand-name">Gilded<br>Slatworks</p>
      <p class="tagline"><span>Shutters</span><span>Shades</span><span>Blinds</span></p>
    </div>
  </section>

  <section class="card card--back" aria-label="Card back">
    <div class="brand">
      <p class="brand-name">Gilded<br>Slatworks</p>
      <p class="tagline"><span>Shutters</span><span>Shades</span><span>Blinds</span></p>
    </div>

    <div class="divider"></div>

    <div class="contact">
      <p class="contact-name">Daniel Trevick</p>
      <p class="contact-role">Owner</p>
      <p class="contact-service">Custom Interior &amp; Exterior<br>Window Treatments</p>
      <p class="contact-line">
        <svg viewBox="0 0 16 16" aria-hidden="true"><path fill="#ffffff" d="M2 6c0-2 2-3 6-3s6 1 6 3v1h-3V5.5H5V7H2zM4 8h8l2 6H2z"/></svg>
        919-555-0148
      </p>
      <p class="contact-line">
        <svg viewBox="0 0 16 16" aria-hidden="true"><circle cx="8" cy="8" r="6.5" fill="none" stroke="#ffffff" stroke-width="1.5"/><path d="M1.5 8h13M8 1.5c-3 3-3 10 0 13M8 1.5c3 3 3 10 0 13" fill="none" stroke="#ffffff" stroke-width="1.2"/></svg>
        GildedSlatworks.com
      </p>
      <p class="contact-note">By Appointment</p>
    </div>
  </section>

</main>
</body>
</html>
```